Business Card Design needed for start up company Halvora

In need of a new business card designed for a start up company based in Sydney, Halvora is a new start up innovative Company, our mission it to make property accessible for everyday Australian and to become the leading Real Estate platform in Australia. We want it to be fresh and clean.

Industry/Entity Type

Financial

Contact Information for Business Card

Section for Name
Section for Title

HALVORA - The Strength of Pooling
Mobile:
Direct:

Font styles to use
Sans Serif

Colors
33a6d7
0692cd
0255a3
ffffff

Requirements
Must have
• Logo, all business card details

```html
<!DOCTYPE html>
<html lang="en">
<head>
<meta charset="utf-8">
<title>Halvora Business Card</title>
<link href="https://fonts.googleapis.com/css2?family=Jost:wght@400;500;600;700&display=swap" rel="stylesheet">
<style>
  :root {
    --stage: #2b2b2d;
    --paper: #f3f3f3;
    --navy: #22407a;
    --sky: #2a9fd9;
    --ink: #555a60;
    --rule: #b9b9b9;
    --white: #ffffff;
  }
  * { margin: 0; padding: 0; box-sizing: border-box; }
  html, body {
    width: 1200px; height: 960px; overflow: hidden;
    background: var(--stage);
    font-family: "Jost", "Futura", sans-serif;
  }
  .canvas { position: relative; width: 1200px; height: 960px; }

  .card {
    position: absolute; width: 600px; height: 342px;
    border-radius: 20px; overflow: hidden;
  }
  .card--front { left: 302px; top: 124px; background: var(--paper); }
  .card--back { left: 299px; top: 493px; background: var(--navy); }

  .brand { position: absolute; display: flex; align-items: center; }
  .brand__dot { border-radius: 50%; background: var(--sky); flex: none; }
  .brand__name { font-weight: 700; letter-spacing: -0.5px; line-height: 1; white-space: nowrap; }

  .card--front .brand { left: 68px; top: 134px; height: 62px; }
  .card--front .brand__dot { width: 62px; height: 62px; margin-right: 8px; }
  .card--front .brand__name { font-size: 34px; color: var(--navy); }

  .card--back .brand { inset: 0; justify-content: center; }
  .card--back .brand__dot { width: 106px; height: 106px; margin-right: 10px; }
  .card--back .brand__name { font-size: 50px; color: var(--white); }

  .divider {
    position: absolute; left: 327px; top: 72px;
    width: 2px; height: 182px;
    background: linear-gradient(to bottom, transparent, var(--rule) 20%, var(--rule) 80%, transparent);
  }

  .details { position: absolute; left: 356px; top: 74px; color: var(--ink); }
  .details__name { font-size: 22px; font-weight: 600; color: var(--navy); line-height: 26px; }
  .details__title { font-size: 15px; color: var(--sky); line-height: 18px; margin-bottom: 9px; }
  .details__address { font-size: 14px; line-height: 18px; margin-bottom: 7px; }
  .contact { list-style: none; font-size: 14px; line-height: 19.5px; }
  .contact li { display: flex; align-items: center; }
  .contact svg { width: 13px; height: 13px; margin-right: 9px; fill: var(--navy); flex: none; }

  .band { position: absolute; left: 0; bottom: 0; width: 600px; height: 35px; }
  .band svg { position: absolute; inset: 0; }
  .band__tagline {
    position: absolute; left: 0; width: 600px; top: 0; line-height: 35px;
    text-align: center; color: var(--white); font-size: 16px;
  }
</style>
</head>
<body>
<main class="canvas">

  <section class="card card--front" aria-label="Business card front">
    <div class="brand">
      <span class="brand__dot"></span>
      <span class="brand__name">HALVORA</span>
    </div>

    <div class="divider"></div>

    <div class="details">
      <p class="details__name">MARA LINDQVIST</p>
      <p class="details__title">CEO/FOUNDER</p>
      <p class="details__address">412 Harbour Street<br>Sydney, NSW 2000</p>
      <ul class="contact">
        <li><svg viewBox="0 0 16 16"><path d="M3.6 1.2l2.2 2.6-1.3 1.9c.9 2 2.6 3.7 4.6 4.6l1.9-1.3 2.6 2.2-1.4 2.6C6.5 13.6 2.4 9.5 1 3.9z"/></svg>02 8123 4567</li>
        <li><svg viewBox="0 0 16 16"><path d="M4 0h8v16H4zM5.3 2v10h5.4V2zM7 13.3h2v1.4H7z" fill-rule="evenodd"/></svg>0412 555 098</li>
        <li><svg viewBox="0 0 16 16"><path d="M1 4h14v1L8 9.5 1 5zM1 6.5l7 4.5 7-4.5V13H1z"/></svg>mara@halvora.com</li>
        <li><svg viewBox="0 0 16 16"><circle cx="8" cy="8" r="7"/><path d="M4 5c1.5 0 2.5 1 2 2.5S4 9 5 11M10 3c0 2 2 2 3 3M9 13c0-2 1.5-3 3-3" stroke="#f3f3f3" stroke-width="1.2" fill="none"/></svg>www.halvora.com</li>
      </ul>
    </div>

    <div class="band">
      <svg viewBox="0 0 600 35" preserveAspectRatio="none">
        <polygon points="0,0 477,0 470,35 0,35" fill="var(--navy)"/>
        <polygon points="477,0 482,0 475,35 470,35" fill="var(--white)"/>
        <polygon points="482,0 600,0 600,35 475,35" fill="var(--sky)"/>
      </svg>
      <p class="band__tagline">The Strength of Pooling</p>
    </div>
  </section>

  <section class="card card--back" aria-label="Business card back">
    <div class="brand">
      <span class="brand__dot"></span>
      <span class="brand__name">HALVORA</span>
    </div>
  </section>

</main>
</body>
</html>
```